Interior Stylist business card design needed

I need a business card for my new company in Sydney called "Liv Harrowby Designs". The business offers an interior styling and colour consultancy. My clients are generally not very design savvy (hence why they use me) and can range from being quite conservative to really wanting something "out there". They can be looking for a budget makeover or something more expensive / substantial. I'd like my business card design to be stylish (but not overly formal). I certainly don't want it to be conservative. I'd like it to stand out a bit! I don't really have any aversion to particular colours and I don't have a logo as such - my business name is really all I have.

Target Market(s)

As above - home owners, ranging from conservative to modern

Industry/Entity Type

Conservative

Contact Information for Business Card

Liv Harrowby Designs
Colour consultancy and interior styling
ph: 0417 238 605
email: livharrowby@qoralnet.net.au

Requirements
Should not have
• Old fashioned writing or motifs. No Times Roman font!!

```html
<!DOCTYPE html>
<html lang="en">
<head>
<meta charset="utf-8">
<title>Liv Harrowby Designs – Business Card</title>
<link rel="stylesheet" href="https://fonts.googleapis.com/css2?family=Cinzel:wght@400;600&family=Open+Sans:wght@400&display=swap">
<style>
  :root {
    --teal: #2d6668;
    --teal-light: #3b7a7b;
    --charcoal: #3c3e3e;
    --paper: #ece9e4;
    --ink-light: #f2f2f0;
    --ink-soft: #d9dedd;
  }
  * { box-sizing: border-box; margin: 0; padding: 0; }
  html, body {
    width: 1200px;
    height: 787px;
    overflow: hidden;
    background: var(--paper);
  }
  .canvas {
    width: 1200px;
    height: 787px;
    display: flex;
    align-items: center;
    justify-content: center;
    gap: 40px;
  }
  .card {
    position: relative;
    width: 540px;
    height: 300px;
    overflow: hidden;
    background: var(--teal);
    box-shadow: 0 6px 18px rgba(0, 0, 0, 0.18);
  }

  /* Contact side */
  .card__shapes {
    position: absolute;
    inset: 0;
    width: 100%;
    height: 100%;
  }
  .brand {
    position: absolute;
    top: 62px;
    left: 190px;
    width: 320px;
    text-align: center;
    color: var(--ink-light);
  }
  .brand__name {
    font-family: "Cinzel", serif;
    font-weight: 600;
    font-size: 26px;
    letter-spacing: 1.5px;
  }
  .brand__tag {
    font-family: "Cinzel", serif;
    font-size: 12px;
    letter-spacing: 9px;
    margin-top: 4px;
  }
  .contact {
    position: absolute;
    left: 24px;
    top: 140px;
    list-style: none;
    font-family: "Open Sans", sans-serif;
    font-size: 12px;
    line-height: 19px;
    color: var(--ink-soft);
  }
  .contact__item { display: flex; align-items: center; gap: 9px; }
  .contact__icon {
    width: 9px;
    height: 9px;
    background: var(--teal-light);
    flex: none;
  }

  /* Name side */
  .panel {
    position: absolute;
    top: 16px;
    left: 18px;
    right: 38px;
    bottom: 24px;
    background: var(--charcoal);
  }
  .signature {
    position: absolute;
    top: 120px;
    left: 18px;
    right: 38px;
    text-align: center;
    color: var(--ink-light);
  }
  .signature__name {
    font-family: "Cinzel", serif;
    font-weight: 600;
    font-size: 24px;
    letter-spacing: 2px;
  }
  .signature__web {
    font-family: "Open Sans", sans-serif;
    font-size: 11px;
    color: var(--ink-soft);
    margin-top: 20px;
  }
</style>
</head>
<body>
<main class="canvas">

  <section class="card card--front" aria-label="Business card front">
    <svg class="card__shapes" viewBox="0 0 540 300" preserveAspectRatio="none" aria-hidden="true">
      <polygon points="0,118 540,238 540,272 300,300 0,300" fill="var(--charcoal)"/>
      <line x1="220" y1="196" x2="540" y2="262" stroke="var(--teal)" stroke-width="2"/>
    </svg>
    <div class="brand">
      <p class="brand__name">Liv Harrowby</p>
      <p class="brand__tag">DESIGNS</p>
    </div>
    <ul class="contact">
      <li class="contact__item"><span class="contact__icon"></span>0417 238 605</li>
      <li class="contact__item"><span class="contact__icon"></span>livharrowby@qoralnet.net.au</li>
      <li class="contact__item"><span class="contact__icon"></span>www.livharrowbydesigns.com.au</li>
    </ul>
  </section>

  <section class="card card--back" aria-label="Business card back">
    <div class="panel"></div>
    <div class="signature">
      <p class="signature__name">LIV HARROWBY</p>
      <p class="signature__web">www.livharrowby.com</p>
    </div>
  </section>

</main>
</body>
</html>
```